Harvest Gateway Fellowship Ministries needs a fresh new web design

We are an up and coming multicultural church that aims to bring people into a life changing encounter with God. We need a fresh and inviting website in order to increase our internet presence and make us easier to connect with.
Here are some of the basic requirements for the site:
• Clearly displayed address, service times, and contact info
• A staff profile page
• An area for a calendar with upcoming events and their details
• Social media buttons
• Group pages for the different ministries (youth, children’s church, men, etc…)
• An area for donations and eCommerce
• A resources page for assorted media (podcasts, sermons, videos, etc.…)
• An area for prayer requests.

```html
<!DOCTYPE html>
<html lang="en">
<head>
<meta charset="utf-8">
<title>Harvest Gateway Fellowship Ministries</title>
<link href="https://fonts.googleapis.com/css2?family=Open+Sans:wght@400;600;700&family=PT+Sans:wght@700&family=Cousine:ital@1&display=swap" rel="stylesheet">
<style>
:root{
  --orange:#f7931e;
  --blue:#1a6fa8;
  --navy:#1c2b3a;
  --navy-dark:#14212e;
  --text:#555;
  --heading:#333;
  --light:#f3f3f3;
  --line:#e2e2e2;
  --white:#fff;
}
*{box-sizing:border-box;margin:0;padding:0}
html,body{width:1200px;height:2521px;overflow:hidden}
body{position:relative;font-family:"Open Sans",Arial,sans-serif;color:var(--text);background:var(--white);font-size:13px}
.abs{position:absolute}
.accent{color:var(--orange)}
.section-title{position:absolute;left:0;width:1200px;text-align:center;font-size:29px;font-weight:400;color:var(--heading)}

/* header */
.site-header{position:absolute;left:0;top:0;width:1200px;height:133px;background:#f7f7f7}
.brand{position:absolute;left:131px;top:30px;display:flex;align-items:center;gap:10px;font-size:17px;font-weight:700;color:var(--navy)}
.brand-mark{width:26px;height:26px;border-radius:50%;background:var(--orange)}
.contact-bar{position:absolute;right:130px;top:22px;display:flex;gap:40px;align-items:center;font-size:13px;color:#666}
.contact-bar span{display:flex;align-items:center;gap:8px}
.contact-bar .phone{font-size:20px;color:var(--blue)}
.main-nav{position:absolute;right:130px;top:74px;display:flex;gap:10px}
.main-nav a{display:block;padding:7px 14px;font-size:13px;color:#444;text-decoration:none;text-transform:uppercase}
.main-nav a.active{background:var(--orange);color:var(--white)}

/* hero */
.hero{position:absolute;left:0;top:133px;width:1200px;height:417px;background:var(--navy)}
.slide{position:absolute;left:131px;top:33px;width:938px;height:347px;background:linear-gradient(100deg,#c9d3dd 0%,#eef1f4 45%,#dfe6ee 70%,#aebccc 100%)}
.slide-photo{position:absolute;right:0;top:0;width:250px;height:347px;background:linear-gradient(180deg,#8ea1b7,#3d4d66)}
.slide-title{position:absolute;left:60px;top:140px;width:590px;text-align:center;font-family:"PT Sans",Arial,sans-serif;font-size:35px;color:#263554}
.slide-text{position:absolute;left:90px;top:200px;width:530px;text-align:center;font-size:13px;line-height:24px;color:#555}
.arrow{position:absolute;top:200px}

/* welcome */
.welcome{position:absolute;left:0;top:550px;width:1200px;height:329px;border-bottom:1px solid var(--line)}
.welcome p{position:absolute;left:138px;width:924px;text-align:center;font-size:13px;line-height:24px;color:#666}

/* staff */
.staff{position:absolute;left:0;top:879px;width:1200px;height:351px;background:var(--light)}
.staff-card{position:absolute;top:126px;width:290px;height:90px}
.staff-photo{position:absolute;left:0;top:0;width:89px;height:87px;background:linear-gradient(160deg,#9b7a63,#4a3327)}
.staff-name{position:absolute;left:110px;top:4px;font-size:13px;font-weight:600;color:var(--blue);text-transform:uppercase}
.staff-bio{position:absolute;left:110px;top:30px;width:180px;font-size:13px;line-height:22px;color:#666}
.btn{position:absolute;background:var(--orange);color:var(--white);font-size:13px;text-align:center;text-transform:uppercase}

/* groups */
.groups{position:absolute;left:0;top:1230px;width:1200px;height:378px;border-bottom:1px solid var(--line)}
.group{position:absolute;top:92px;width:219px;text-align:center}
.group-photo{width:219px;height:146px}
.group-name{margin-top:24px;font-size:13px;font-weight:600;color:var(--blue);text-transform:uppercase}
.group-text{margin-top:10px;font-size:13px;line-height:22px;color:#666}

/* media + events */
.media-events{position:absolute;left:0;top:1608px;width:1200px;height:469px;background:var(--light)}
.video{position:absolute;left:131px;top:71px;width:450px;height:331px;background:linear-gradient(120deg,#6f6f70,#9a9ea3 55%,#7c8188)}
.events-card{position:absolute;left:615px;top:71px;width:454px;height:331px;background:var(--white);border:1px solid var(--line)}
.events-card h2{position:absolute;left:20px;top:16px;font-size:23px;font-weight:400;color:var(--heading)}
.events-card hr{position:absolute;left:0;top:55px;width:452px;border:0;border-top:1px solid var(--line)}
.month{position:absolute;left:0;top:75px;width:454px;text-align:center;font-family:"PT Sans",Arial,sans-serif;font-size:20px;color:#222}
.calendar{position:absolute;left:16px;top:110px;width:420px;border-collapse:collapse;font-family:Arial,sans-serif}
.calendar th{background:#ddd;font-family:"Cousine",monospace;font-style:italic;font-weight:400;font-size:13px;height:20px;color:#333}
.calendar td{height:28px;text-align:center;font-size:14px;font-weight:700;color:#222;border-bottom:1px solid #999}
.calendar td.muted{color:#ccc;font-weight:400;border-bottom:0}
.calendar tr:last-child td{border-bottom:0}
.get-detail{position:absolute;right:16px;top:298px;font-size:13px;color:var(--orange)}

/* prayer + donation */
.prayer{position:absolute;left:131px;top:2120px;width:460px}
.prayer h2{font-size:23px;font-weight:400;color:var(--heading)}
.prayer-subject{position:absolute;top:72px;font-size:13px;color:var(--blue)}
.prayer-text{position:absolute;top:90px;width:440px;font-size:13px;line-height:23px;color:#666}
.prayer-meta{position:absolute;top:175px;width:458px;height:40px;background:var(--light);display:flex;align-items:center;gap:40px;padding-left:16px;font-size:13px;color:#666}
.donation{position:absolute;left:622px;top:2120px;width:447px;height:224px;background:#f1f1f1}
.donation h2{position:absolute;left:74px;top:22px;font-size:23px;font-weight:400;color:var(--heading)}
.field{position:absolute;width:188px;height:34px;background:var(--white);border:1px solid #ddd;font-size:12px;color:#aaa;padding:8px 12px;display:flex;justify-content:space-between}
.card-badge{position:absolute;top:182px;width:32px;height:20px;border-radius:2px}

/* footer */
.site-footer{position:absolute;left:0;top:2403px;width:1200px;height:118px;background:var(--navy)}
.footer-links{position:absolute;left:131px;top:36px;font-size:13px;color:#c9d1da}
.copyright{position:absolute;left:131px;top:70px;font-size:11px;color:#8d9aa8}
.social{position:absolute;left:913px;top:46px;display:flex;gap:6px}
.social span{width:34px;height:34px;border-radius:50%;border:2px solid #cfd6dd;background:#e8ecef}
</style>
</head>
<body>

<header class="site-header">
  <div class="brand"><span class="brand-mark"></span>Harvest Gateway Fellowship Ministries</div>
  <div class="contact-bar">
    <span><svg width="16" height="12" viewBox="0 0 16 12"><rect x="1" y="3" width="14" height="8" rx="1" fill="#aaa"/><rect x="3" y="0" width="10" height="3" rx="1" fill="#aaa"/></svg>Call Us : <b class="phone" style="font-weight:400">555.014.2280</b></span>
    <span><svg width="16" height="12" viewBox="0 0 16 12"><rect x="0" y="0" width="16" height="12" fill="#aaa"/><path d="M0 0L8 7L16 0" stroke="#fff" fill="none"/></svg>info@harvestgateway.org</span>
  </div>
  <nav class="main-nav">
    <a class="active">Home</a><a>About Us</a><a>Events</a><a>Prayer Request</a><a>Donate</a><a>Contact Us</a>
  </nav>
</header>

<section class="hero">
  <svg class="arrow" style="left:86px" width="18" height="34" viewBox="0 0 18 34"><path d="M16 2L3 17L16 32" stroke="#fff" stroke-width="3" fill="none"/></svg>
  <div class="slide">
    <div class="slide-photo" role="img" aria-label="Smiling couple standing together"></div>
    <h1 class="slide-title">Harvest Gateway Fellowship Ministries</h1>
    <p class="slide-text">Neque porro quisquam est qui dolorem ipsum quia dolor sit amet, consectetur, adipisci velit Neque porro quisquam est qui dolorem ipsum quia dolor sit amet, consectetur</p>
  </div>
  <svg class="arrow" style="left:1096px" width="18" height="34" viewBox="0 0 18 34"><path d="M2 2L15 17L2 32" stroke="#8c99a8" stroke-width="3" fill="none"/></svg>
</section>

<section class="welcome">
  <h2 class="section-title" style="top:74px">Welcome to <span class="accent">HGFM</span></h2>
  <p style="top:134px">Welcome to Harvest Gateway Fellowship Ministries, a place where we can come together and fellowship. HGFM is located in Maple Grove, Ohio and we would love to have you worship with us. We believe God is doing something extraordinary through our church and would like for you to be a part. Please prayerfully consider our church as a place you would like to worship and fellowship with us as we continue to grow.</p>
  <p style="top:234px">As you venture on our website please feel free to contact us through email, phone, or leave a prayer request for us to pray on your behalf. Please take a minute and look at our upcoming events. <span class="accent">We hope you will visit us real soon.</span></p>
</section>

<section class="staff">
  <h2 class="section-title" style="top:48px">Our <span class="accent">Staff</span></h2>
  <div class="staff-card" style="left:131px"><div class="staff-photo" role="img" aria-label="Portrait of staff member Amara"></div><div class="staff-name">Amara</div><p class="staff-bio">Neque porro quisquam est qu dolorem ipsum quia dolor situ amet, consectetur.</p></div>
  <div class="staff-card" style="left:452px"><div class="staff-photo" role="img" aria-label="Portrait of staff member Daniel"></div><div class="staff-name">Daniel</div><p class="staff-bio">Neque porro quisquam est qu dolorem ipsum quia dolor situ amet, consectetur.</p></div>
  <div class="staff-card" style="left:771px"><div class="staff-photo" role="img" aria-label="Portrait of staff member Grace"></div><div class="staff-name">Grace</div><p class="staff-bio">Neque porro quisquam est qu dolorem ipsum quia dolor situ amet, consectetur.</p></div>
  <div class="btn" style="left:540px;top:262px;width:119px;height:37px;line-height:37px">View More</div>
</section>

<section class="groups">
  <h2 class="section-title" style="top:28px">View <span class="accent">Group's</span></h2>
  <div class="group" style="left:131px"><div class="group-photo" role="img" aria-label="Teenagers smiling together" style="background:linear-gradient(135deg,#7fa36a,#3f5e35)"></div><div class="group-name">Youth Group</div><p class="group-text">Neque porro quisquam est qu dolor ipsum quia dolor situ amet.</p></div>
  <div class="group" style="left:370px"><div class="group-photo" role="img" aria-label="Children reading together in class" style="background:linear-gradient(135deg,#b07c66,#d9b7a6)"></div><div class="group-name">Children's Church</div><p class="group-text">Neque porro quisquam est qu dolor ipsum quia dolor situ amet.</p></div>
  <div class="group" style="left:610px"><div class="group-photo" role="img" aria-label="White church building against blue sky" style="background:linear-gradient(180deg,#5f8fc4,#c7d9ea 70%,#d8b98f)"></div><div class="group-name">Religious Group</div><p class="group-text">Neque porro quisquam est qu dolor ipsum quia dolor situ amet.</p></div>
  <div class="group" style="left:850px"><div class="group-photo" role="img" aria-label="Man in suit standing in office" style="background:linear-gradient(135deg,#8fb4c9,#2f4f6e)"></div><div class="group-name">Man Group</div><p class="group-text">Neque porro quisquam est qu dolor ipsum quia dolor situ amet.</p></div>
</section>

<section class="media-events">
  <div class="video" role="img" aria-label="Video still of a man smiling in a meeting">
    <svg style="position:absolute;left:192px;top:132px" width="70" height="70" viewBox="0 0 70 70"><circle cx="35" cy="35" r="32" stroke="#fff" stroke-width="5" fill="none"/><path d="M27 20L51 35L27 50Z" fill="#fff"/></svg>
  </div>
  <div class="events-card">
    <h2>Upcoming <span class="accent">Events</span></h2>
    <hr>
    <div class="month">JUNE</div>
    <table class="calendar">
      <tr><th>Sun</th><th>Mon</th><th>Tue</th><th>Wed</th><th>Thu</th><th>Fri</th><th>Sat</th></tr>
      <tr><td>1</td><td>2</td><td>3</td><td>4</td><td>5</td><td>6</td><td>7</td></tr>
      <tr><td>8</td><td>9</td><td>10</td><td>11</td><td>12</td><td>13</td><td>14</td></tr>
      <tr><td>15</td><td>16</td><td>17</td><td>18</td><td>19</td><td>20</td><td>21</td></tr>
      <tr><td>22</td><td>23</td><td>24</td><td>25</td><td>26</td><td>27</td><td>28</td></tr>
      <tr><td>29</td><td>30</td><td class="muted">1</td><td class="muted">2</td><td class="muted">3</td><td class="muted">4</td><td class="muted">5</td></tr>
    </table>
    <div class="get-detail">Get Detail &gt;&gt;</div>
  </div>
</section>

<section class="prayer">
  <h2>View <span class="accent">Prayer</span> Listing</h2>
  <div class="prayer-subject">Unspoken request</div>
  <p class="prayer-text">As you venture on our website please feel free to contact us through email, phone, or leave a prayer request for us to pray on your behalf would like to worship and fellowship with us as we continue to grow.</p>
  <div class="prayer-meta"><span>Viewed <span class="accent">(325)</span></span><span>Prayer Requested By: <span class="accent">Marcus, 03-28-2012 - 11:08:41 AM</span></span></div>
</section>

<section class="donation">
  <svg style="position:absolute;left:24px;top:22px" width="36" height="36" viewBox="0 0 36 36"><rect width="36" height="36" rx="6" fill="#3aa64a"/><text x="18" y="27" text-anchor="middle" font-family="Arial" font-weight="700" font-size="24" fill="#fff">$</text></svg>
  <h2>Give <span style="color:var(--blue)">Donation</span></h2>
  <div class="field" style="left:22px;top:80px">Enter Name</div>
  <div class="field" style="left:236px;top:80px">Enter Email</div>
  <div class="field" style="left:22px;top:126px">---Enter Amount---<span>▾</span></div>
  <div class="field" style="left:236px;top:126px">---Select USD---<span>▾</span></div>
  <div class="card-badge" style="left:173px;background:#2c5ea8"></div>
  <div class="card-badge" style="left:210px;background:#d9d9d9"></div>
  <div class="card-badge" style="left:247px;background:#3b8fd1"></div>
  <div class="card-badge" style="left:284px;background:#e6e6e6"></div>
  <div class="btn" style="left:338px;top:172px;width:86px;height:35px;line-height:35px">Submit</div>
</section>

<footer class="site-footer">
  <div class="footer-links">Privacy Policy &nbsp;/ &nbsp;Terms Conditions &nbsp;/ &nbsp;Sitemap &nbsp;/ &nbsp;Contact Us</div>
  <div class="copyright">© 2014 HGFM. All Rights Reserved, Site Developed by Northlight Studio</div>
  <div class="social"><span></span><span></span><span></span><span></span></div>
</footer>

</body>
</html>
```